New Business Card Design Project

We require a business card design for Vexalund, a newly established Indian company.
Our focus is on the development, manufacturing, and export of a diverse array of pharmaceutical products on a global scale. The card should convey a professional appearance, as our primary markets are in Africa, China, and Southeast Asian nations.
We envision a two-sided business card, with the reverse side dedicated to a logo set against a solid color or an elegantly designed pattern. The corners should be rounded. We would appreciate seeing both horizontal and vertical design options. We trust the designer to utilize their expertise in creating this design.

The content for the business card is included in the attached Word file.

Target Market(s)

Our primary markets are in Africa, China, and Southeast Asian, Latin America, Maldives, Sri Lanka

Industry/Entity Type

Pharmaceutical Manufacturing and Export

Contact Information for Business Card

Colors

Designer to choose colors to be used in the design.

Requirements
Must have
• The reverse side of the business card features solely the logo along with the tagline, "Care in Every Dose."
Should not have
• The logo should not exceed two instances, encompassing both the front and back sides of the card.

```html
<!DOCTYPE html>
<html lang="en">
<head>
<meta charset="utf-8">
<title>Vexalund Business Card</title>
<link rel="stylesheet" href="https://fonts.googleapis.com/css2?family=Open+Sans:wght@400;600;700&family=Poppins:wght@400&display=swap">
<style>
  :root {
    --stage: #232323;
    --card-dark: #1d1e21;
    --brand-blue: #2aa4dd;
    --brand-red: #ea5a48;
    --red-deep: #d94c3b;
    --red-soft: #ef6a58;
    --ink-light: #f1f1f1;
  }
  * { margin: 0; padding: 0; box-sizing: border-box; }
  html, body {
    width: 1200px;
    height: 780px;
    overflow: hidden;
    background: var(--stage);
  }
  .canvas {
    position: relative;
    width: 1200px;
    height: 780px;
    display: flex;
    align-items: center;
    justify-content: center;
    gap: 40px;
  }
  .card {
    position: relative;
    width: 540px;
    height: 310px;
    border-radius: 22px;
    overflow: hidden;
    box-shadow: 0 18px 40px rgba(0,0,0,0.45);
  }

  /* Front side */
  .card-front {
    background: var(--card-dark);
    font-family: "Open Sans", sans-serif;
  }
  .accent-bar-left {
    position: absolute;
    left: 26px;
    top: 0;
    width: 6px;
    height: 124px;
    background: var(--brand-red);
  }
  .accent-bar-right {
    position: absolute;
    right: 20px;
    bottom: 0;
    width: 12px;
    height: 130px;
    background: var(--brand-red);
  }
  .brand-name {
    position: absolute;
    left: 44px;
    top: 112px;
    font-weight: 700;
    font-size: 38px;
    line-height: 1;
    letter-spacing: -0.5px;
    color: var(--brand-blue);
  }
  .divider {
    position: absolute;
    left: 236px;
    top: 110px;
    width: 40px;
    height: 120px;
  }
  .person {
    position: absolute;
    left: 290px;
    top: 92px;
  }
  .person-name {
    font-size: 24px;
    line-height: 1.1;
    white-space: nowrap;
  }
  .person-name .given {
    color: var(--brand-blue);
    font-weight: 700;
  }
  .person-name .family {
    color: var(--brand-red);
    font-weight: 400;
  }
  .person-title {
    margin-top: 2px;
    font-size: 13px;
    color: var(--ink-light);
    letter-spacing: 0.5px;
  }
  .contact-list {
    position: absolute;
    left: 278px;
    top: 160px;
    list-style: none;
  }
  .contact-item {
    display: flex;
    align-items: center;
    gap: 8px;
    font-size: 12.5px;
    color: var(--ink-light);
    height: 22px;
    white-space: nowrap;
  }
  .contact-icon {
    width: 13px;
    height: 13px;
    flex: none;
  }
  .address {
    position: absolute;
    left: 44px;
    top: 262px;
    font-size: 12.5px;
    color: var(--brand-blue);
    letter-spacing: 0.2px;
    white-space: nowrap;
  }

  /* Back side */
  .card-back {
    background: var(--brand-red);
  }
  .back-pattern {
    position: absolute;
    inset: 0;
    background: linear-gradient(160deg, var(--red-soft) 0%, var(--brand-red) 45%, var(--red-deep) 100%);
  }
  .back-brand {
    position: absolute;
    right: 40px;
    top: 136px;
    font-family: "Open Sans", sans-serif;
    font-weight: 700;
    font-size: 15px;
    color: #ffffff;
  }
  .tagline {
    position: absolute;
    left: 40px;
    bottom: 36px;
    font-family: "Poppins", sans-serif;
    font-size: 15px;
    color: #ffffff;
    letter-spacing: 0.3px;
    white-space: nowrap;
  }
</style>
</head>
<body>
<main class="canvas">

  <section class="card card-front" aria-label="Business card front">
    <span class="accent-bar-left"></span>
    <span class="accent-bar-right"></span>

    <p class="brand-name">Vexalund</p>

    <svg class="divider" viewBox="0 0 40 120" aria-hidden="true">
      <line x1="38" y1="0" x2="2" y2="120" stroke="var(--brand-blue)" stroke-width="1"/>
    </svg>

    <div class="person">
      <p class="person-name"><span class="given">Arvind</span> <span class="family">K. Solanke</span></p>
      <p class="person-title">CEO</p>
    </div>

    <ul class="contact-list">
      <li class="contact-item">
        <svg class="contact-icon" viewBox="0 0 13 13" aria-hidden="true">
          <rect x="1.5" y="1.5" width="10" height="10" fill="none" stroke="var(--brand-red)" stroke-width="1.4"/>
        </svg>
        <span>+919 503118472</span>
      </li>
      <li class="contact-item">
        <svg class="contact-icon" viewBox="0 0 13 13" aria-hidden="true">
          <circle cx="6.5" cy="6.5" r="5.5" fill="none" stroke="var(--brand-blue)" stroke-width="1.3"/>
          <ellipse cx="6.5" cy="6.5" rx="2.4" ry="5.5" fill="none" stroke="var(--brand-blue)" stroke-width="1"/>
          <line x1="1" y1="6.5" x2="12" y2="6.5" stroke="var(--brand-blue)" stroke-width="1"/>
        </svg>
        <span>www.vexalund.com</span>
      </li>
      <li class="contact-item">
        <svg class="contact-icon" viewBox="0 0 13 13" aria-hidden="true">
          <rect x="1" y="3" width="11" height="8" fill="var(--brand-red)"/>
          <polyline points="1,3 6.5,7.5 12,3" fill="none" stroke="var(--card-dark)" stroke-width="1"/>
        </svg>
        <span>asolanke@vexalund.com</span>
      </li>
    </ul>

    <p class="address">7, Sundaram Nagar, Karanpur, 441208, India</p>
  </section>

  <section class="card card-back" aria-label="Business card back">
    <div class="back-pattern" role="img" aria-label="Repeating pattern of small capsule marks in tones of red"></div>
    <p class="back-brand">Vexalund</p>
    <p class="tagline">Care in Every Dose.</p>
  </section>

</main>
</body>
</html>
```